Marlowe Group needs a business card

I would like the card to be simple but modern and elegant.
I like black and white.
or black and gold.
we are a private finance lender and also are involved in property and property developments.

please look at the business card photos i provided i would like M.G only one one side and all the other details on the other side use fonts that tie in with my theme.

Industry/Entity Type

Finance

Contact Information for Business Card

Marlowe Group (M.G) Daniel Marlowe M: 0413586207 E: danmarl@inboxmail.test

Font styles to use
Other font styles liked:
• Use fonts that would reflect our business

Colors
000000
ffffff

Requirements
Must have
• one side of details
• other side has either M.G or Marlowe Group like in the photos provided

```html
<!DOCTYPE html>
<html lang="en">
<head>
<meta charset="utf-8">
<title>Marlowe Group – Business Card</title>
<link rel="stylesheet" href="https://fonts.googleapis.com/css2?family=Cinzel:wght@400;700&family=Lato:wght@400&display=swap">
<style>
  :root {
    --backdrop: #6d6d6d;
    --gold-deep: #ffcb35;
    --gold-light: #fde8a6;
    --gold-ink: #e8b923;
    --black: #050509;
    --ink: #111111;
    --shadow: rgba(0, 0, 0, 0.35);
  }
  * { margin: 0; padding: 0; box-sizing: border-box; }
  html, body {
    width: 1200px;
    height: 900px;
    overflow: hidden;
    background: var(--backdrop);
  }
  .stage { position: relative; width: 1200px; height: 900px; }
  .card {
    position: absolute;
    top: 271px;
    width: 457px;
    height: 282px;
    border-radius: 14px;
    box-shadow: 2px 3px 6px var(--shadow);
    overflow: hidden;
  }
  .card--front {
    left: 137px;
    background: linear-gradient(90deg,
      var(--gold-deep) 0%,
      var(--gold-deep) 38%,
      var(--gold-light) 58%,
      var(--gold-light) 72%,
      var(--gold-deep) 90%,
      var(--gold-deep) 100%);
    color: var(--ink);
  }
  .card--back {
    left: 626px;
    background:
      radial-gradient(ellipse 90px 110px at 58% 100%, rgba(255,255,255,0.16), transparent 70%),
      radial-gradient(ellipse 260px 180px at 55% 50%, #14141a, transparent 80%),
      var(--black);
  }
  .brand-mark {
    position: absolute;
    left: 0; right: 0;
    text-align: center;
    font-family: "Cinzel", serif;
    font-weight: 400;
    letter-spacing: 4px;
  }
  .card--front .brand-mark { top: 52px; font-size: 58px; color: var(--ink); }
  .card--back .brand-mark { top: 78px; font-size: 64px; color: var(--gold-ink); }
  .holder-name {
    position: absolute;
    top: 182px; left: 0; right: 0;
    text-align: center;
    font-family: "Cinzel", serif;
    font-weight: 700;
    font-size: 16px;
    letter-spacing: 0.5px;
  }
  .name-rule {
    position: absolute;
    top: 211px; left: 163px;
    width: 130px; height: 1px;
    background: linear-gradient(90deg, transparent, rgba(0,0,0,0.55), transparent);
  }
  .contact-line {
    position: absolute;
    top: 221px; left: 0; right: 0;
    text-align: center;
    font-family: "Lato", sans-serif;
    font-size: 13px;
  }
  .contact-line .divider { margin: 0 3px 0 6px; }
  .company-name {
    position: absolute;
    top: 192px; left: 0; right: 0;
    text-align: center;
    font-family: "Cinzel", serif;
    font-weight: 400;
    font-size: 20px;
    color: var(--gold-ink);
    letter-spacing: 0.5px;
  }
</style>
</head>
<body>
  <main class="stage">
    <section class="card card--front" aria-label="Card front with contact details">
      <div class="brand-mark">M.G</div>
      <h1 class="holder-name">DANIEL MARLOWE</h1>
      <div class="name-rule"></div>
      <p class="contact-line">M: 0413586207 <span class="divider">|</span> E: danmarl@inboxmail.test</p>
    </section>
    <section class="card card--back" aria-label="Card back with company name">
      <div class="brand-mark">M.G</div>
      <p class="company-name">Marlowe Group</p>
    </section>
  </main>
</body>
</html>
```